Commercial Rooftop Solar business needs a website

We need a website with fantastic appeal for a new company based in Melbourne called Tallow Ridge Energy. We design and install solar energy systems for commercial applications across Australia. Our market is to focus on small to medium businesses looking for solar solutions, but we will also provide our service for residential customers. We would like a beautiful 'front page' feel to our home page, using photographs of solar PV systems and/or natural imagery. Our logo uses the colours orange and black, which could easily be echoed in photographic imagery of sunset and sunrise, for example. The design should communicate quiet confidence and professionalism to a corporate marketplace.

NEW POINTS FOR BRIEF: This design also needs to be flexible to allow for additional future content, including a Support page with sub pages, FAQ's, and a Blog.

As part of this design project, we will require the coding for the website to be completed by the designer.

We have seen some websites, which we like the look and feel of: these are listed below.

brightvanepower.com.au:

• Beautiful images underlaying brief text selling points.
• Simple ‘front cover’ style home page with elegant drop-down menu, stylish simple font style.
• Home page invites exploration through the menu links, rather than trying to provide all the information up front.
• Company logo and name in the top left hand corner, contact details accessible at top right hand, seems consistent in most sites.

kelpworks.com.au

rumbofield.com:
• Same element as the others is the front-page style home page with beautiful images underlying text.

We have a webpage that we started uploading content to. You can use some of the content there in your designs: www.tallowridgeenergy.com.au

Technical Specifications:
PAGES:

Home

About Us

Solutions - Commercial
- Residential

Products - Solar Panels - Vorla Heron, Vorla TELD, Vorla QB
- Solar Inverters - Kestamo, BrilQuill
- Monitoring systems - Dunmere Metrics
- Batteries - RW

- Datasheets have been provided for reference but if it's too much work, you can use generic text and we will provide content later.

Contact Us

FUTURE PAGES (Please consider in structure, where links could be placed):

Support

FAQ's

Blog.

We could provide some content for the Support page soon, but the Blog and FAQ's are future pages which we don't want highlighted in the design as we don't yet have content.

Phone: 1800 7 BIRCH
Email: sales@tallowridgeenergy.com.au

Currently, I do not have images and text available. Please
use placeholders in the meantime. The final text and images will be uploaded for the winner once a winning design has been selected.

Target Market(s)

Primary focus is on small to medium sized business owners. Those owners will have a house which may be suitable for solar so we want to cater to residential deeper in the website.

Industry/Entity Type

Solar Energy

Coding

Coded - Design and coding required

Number of Pages Required

5+ page

Colors
f78f20
0255a3

Requirements
Must have
• Logo as per attachments.
Nice to have
• Logo can have alternate colours Eg. White on Orange or Black etc. provided colour correct logo is shown somewhere eg. footer or contact page.
• In the active site, I'd like to have:
• Very slowly zooming images - barely perceptible.
• Title text that rolls into place
• Subtle movements
• See https://plumtally.com.au/ for example

```html
<!DOCTYPE html>
<html lang="en">
<head>
<meta charset="utf-8">
<title>Tallow Ridge Energy – Commercial Solar</title>
<link href="https://fonts.googleapis.com/css2?family=Michroma&family=Open+Sans:wght@400;600;700&display=swap" rel="stylesheet">
<style>
:root{
  --accent:#f03a17;
  --ink:#222222;
  --text:#3a3a3a;
  --white:#ffffff;
  --footer:#1b1b1b;
  --footer-base:#0e0e0e;
  --footer-line:#3a3a3a;
  --footer-text:#e6e6e6;
}
*{margin:0;padding:0;box-sizing:border-box}
html,body{width:1097px;height:1200px;overflow:hidden}
body{position:relative;font-family:'Open Sans',sans-serif;color:var(--text);background:var(--white)}
.wide{font-family:'Michroma',sans-serif;white-space:nowrap}

/* hero */
.hero{position:absolute;left:0;top:0;width:1097px;height:415px;
  background:linear-gradient(180deg,#3a5f8e 0%,#5f7fa3 25%,#7a6a5c 45%,#8a5a45 58%,#a88a6a 72%,#c3a57e 100%)}
.hero-shade{position:absolute;inset:0;background:rgba(20,25,35,.28)}
.brand{position:absolute;left:148px;top:40px;width:160px;color:var(--white);
  font-weight:700;font-size:20px;line-height:24px;display:flex;align-items:center;gap:8px}
.brand-dot{width:14px;height:14px;border-radius:50%;background:var(--white);flex:none}
.topbar{position:absolute;right:138px;top:19px;display:flex;align-items:center;gap:13px}
.phone{display:flex;align-items:center;gap:6px;color:var(--white);font-weight:700;font-size:15px}
.quote{display:flex;align-items:center;gap:8px;height:28px;padding:0 12px 0 13px;border-radius:14px;
  background:var(--accent);border:1.5px solid var(--white);color:var(--white);font-weight:600;font-size:14px}
.nav{position:absolute;right:138px;top:76px;display:flex;gap:33px;font-size:10.5px;letter-spacing:1.3px;color:var(--white)}
.nav .active{color:var(--accent)}
.caret{display:inline-block;border:3.5px solid transparent;border-top-color:currentColor;margin-left:4px;vertical-align:-1px}
.dropdown{position:absolute;left:477px;top:97px;width:114px;height:61px;background:var(--white);
  font-size:8px;letter-spacing:.6px}
.dropdown::before{content:"";position:absolute;right:8px;top:-6px;border:6px solid transparent;border-top:0;border-bottom-color:var(--white)}
.dropdown a{display:block;padding-left:17px;height:30px;line-height:30px;color:var(--ink);text-decoration:none}
.dropdown a.current{color:var(--accent);border-bottom:1px dashed #ddd;margin:0 4px;padding-left:13px}
.hero-title{position:absolute;left:0;top:216px;width:1097px;text-align:center;color:var(--white);
  font-weight:600;font-size:25.5px;line-height:32px}

/* content */
.section-title{position:absolute;left:0;top:460px;width:1097px;display:flex;justify-content:center;align-items:center;gap:12px;
  font-size:24px;color:var(--ink);letter-spacing:2px}
.section-title::before,.section-title::after{content:"";width:68px;height:1.5px;background:var(--ink)}
.copy{position:absolute;left:150px;top:546px;width:810px}
.copy h3{color:var(--accent);font-weight:400;font-size:15.5px;line-height:20px;margin-bottom:5px}
.copy p{font-size:11.1px;line-height:19.8px;margin-bottom:23px}
.cta{position:absolute;left:150px;top:884px;width:283px;height:30px;border-radius:15px;background:var(--accent);
  color:var(--white);font-size:8.6px;letter-spacing:1.2px;display:flex;align-items:center;justify-content:space-between;padding:0 5px 0 11px}
.cta-arrow{width:20px;height:20px;border-radius:50%;background:var(--white);display:flex;align-items:center;justify-content:center;flex:none}

/* footer */
.footer{position:absolute;left:0;top:953px;width:1097px;height:209px;background:var(--footer);color:var(--footer-text)}
.col-title{position:absolute;top:28px;font-size:11px;letter-spacing:1.6px;color:var(--white);padding-bottom:8px;border-bottom:1px dashed #666}
.divider{position:absolute;top:46px;width:1px;height:145px;background:var(--footer-line)}
.links{position:absolute;left:150px;top:68px;list-style:none;font-size:11px}
.links li{height:29px;padding-left:10px;position:relative}
.links li::before{content:"›";position:absolute;left:0;color:#777}
.field{position:absolute;left:336px;width:174px;background:var(--white);border-radius:2px;font-size:9px;color:#555;padding:3px 5px}
.submit{position:absolute;left:336px;top:174px;width:62px;height:20px;border-radius:10px;background:var(--accent);
  color:var(--white);font-size:7.5px;letter-spacing:1px;display:flex;align-items:center;justify-content:center}
.contact{position:absolute;left:558px;top:63px;width:184px;font-size:11.5px}
.contact li{list-style:none;display:flex;gap:8px;align-items:flex-start;height:32px;padding-top:6px;border-bottom:1px solid #2e2e2e;white-space:nowrap}
.contact li:last-child{border:0}
.foot-brand{position:absolute;left:820px;top:70px;width:135px;text-align:center;color:var(--white);font-weight:700;font-size:18px;line-height:23px}
.abn{position:absolute;left:800px;top:178px;width:175px;text-align:center;font-size:11px;color:var(--white)}
.base{position:absolute;left:0;top:1162px;width:1097px;height:38px;background:var(--footer-base);color:#ddd;
  font-size:10px;text-align:center;line-height:38px}
</style>
</head>
<body>

<header class="hero" role="img" aria-label="Photograph of a long brick industrial building with solar panels on its roof under a blue sky">
  <div class="hero-shade"></div>
</header>

<div class="brand"><span class="brand-dot"></span>Tallow Ridge Energy</div>

<div class="topbar">
  <div class="phone">
    <svg width="27" height="27" viewBox="0 0 27 27"><circle cx="13.5" cy="13.5" r="12.5" fill="none" stroke="#fff" stroke-width="1.6"/><path d="M9 7.5l2.5-.5 1.5 3.5-1.8 1.2a8 8 0 0 0 3.6 3.6l1.2-1.8 3.5 1.5-.5 2.5c-5 .5-10.5-5-10-10z" fill="#fff"/></svg>
    1800 7 BIRCH
  </div>
  <div class="quote">FREE QUOTE
    <svg width="20" height="20" viewBox="0 0 20 20" fill="none" stroke="#fff" stroke-width="1.3"><rect x="3" y="2" width="11" height="15" rx="1"/><path d="M6 7h5M6 10h5M6 13h3M17 8l-6 8-1.5.5.3-1.6 6-8z"/></svg>
  </div>
</div>

<nav class="nav wide">
  <span>HOME</span>
  <span class="active">SOLUTIONS<i class="caret"></i></span>
  <span>PRODUCTS<i class="caret"></i></span>
  <span>ABOUT US</span>
  <span>CONTACT US</span>
</nav>

<div class="dropdown wide">
  <a class="current">COMMERCIAL</a>
  <a>RESIDENTIAL</a>
</div>

<h1 class="hero-title">Tallow Ridge Energy Is A National Company That<br>Specialises In Solar Solutions For The Commercial<br>And Residential</h1>

<h2 class="section-title wide">COMMERCIAL</h2>

<main class="copy">
  <h3>Tallow Ridge Energy specialises in energy solutions for small to medium businesses.</h3>
  <p>In a sunburnt country, harnessing the immense power of the sun for the energy requirements of your business is the most practical solution to sustain your business for the long term. This is energy that never runs out. Ask us how we can reduce your operating costs and protect your business from ever increasing electricity prices.</p>
  <h3>Business Case: No-Cost Solar.</h3>
  <p>There’s an incredibly sound business case to install solar for your business. With the current Government incentives, provided as up-front rebates based on Small-scale Technology Certificates (STCs), solar electricity systems can be bought or leased cost-effectively, and even potentially provide income through production and export of power to the grid. The result is no-cost solar, the cost being completely off-set by incentives and savings in electricity costs. We offer finance so we can provide your solar energy solution promptly and with effectively no up-front cost to your business.</p>
  <h3>Sustainability: Our Environment Matters.</h3>
  <p>Protecting our planet protects all of us: our communities, our health and our future. Using sustainable energy ensures the longevity of our businesses too. Switching to solar power is an investment in the future health of every part of our community life and activity, including the running of a healthy business.</p>
</main>

<div class="cta wide"><span>REQUEST A FREE CONSULTATION</span>
  <span class="cta-arrow"><svg width="8" height="8" viewBox="0 0 8 8"><path d="M2.5 1l3 3-3 3" fill="none" stroke="#222" stroke-width="1.6"/></svg></span>
</div>

<footer class="footer">
  <div class="col-title wide" style="left:154px">QUICK LINKS</div>
  <div class="divider" style="left:295px"></div>
  <ul class="links">
    <li>Home</li><li>Solutions</li><li>Products</li><li>About Us</li><li>Contact Us</li>
  </ul>

  <div class="col-title wide" style="left:336px;width:175px">QUICK INQUIRY</div>
  <div class="divider" style="left:532px"></div>
  <div class="field" style="top:63px;height:18px">Name</div>
  <div class="field" style="top:86px;height:18px">Email</div>
  <div class="field" style="top:110px;height:57px">Message</div>
  <div class="submit wide">SUBMIT</div>

  <div class="col-title wide" style="left:558px;width:184px">CONTACT DETAILS</div>
  <div class="divider" style="left:783px"></div>
  <ul class="contact">
    <li><svg width="11" height="11" viewBox="0 0 11 11"><path d="M1.5 1l2.3-.4 1.2 2.6-1.3 1a5.5 5.5 0 0 0 2.7 2.7l1-1.3 2.6 1.2-.4 2.3C5 9.7.6 5.3 1.5 1z" fill="var(--accent)"/></svg>1800 7 BIRCH</li>
    <li><svg width="12" height="11" viewBox="0 0 12 11"><rect x="0.5" y="2" width="11" height="7.5" fill="var(--accent)"/><path d="M.5 2l5.5 4 5.5-4" fill="none" stroke="#1b1b1b" stroke-width="1"/></svg>info@tallowridgeenergy.com.au</li>
    <li><svg width="11" height="11" viewBox="0 0 11 11" fill="none" stroke="var(--accent)" stroke-width="1"><circle cx="5.5" cy="5.5" r="4.8"/><path d="M.7 5.5h9.6M5.5.7c-2.6 3-2.6 6.6 0 9.6M5.5.7c2.6 3 2.6 6.6 0 9.6"/></svg>www.tallowridgeenergy.com.au</li>
    <li><svg width="11" height="13" viewBox="0 0 11 13"><path d="M5.5 0a4.5 4.5 0 0 1 4.5 4.5c0 3.2-4.5 8.5-4.5 8.5S1 7.7 1 4.5A4.5 4.5 0 0 1 5.5 0z" fill="var(--accent)"/><circle cx="5.5" cy="4.5" r="1.6" fill="#1b1b1b"/></svg><span><b style="font-size:12.5px;color:#fff">TALLOW RIDGE ENERGY</b><br>Kelbrook, Victoria</span></li>
  </ul>

  <div class="foot-brand">Tallow Ridge<br>Energy</div>
  <div class="abn">ABN: 41 502 778 164</div>
</footer>

<div class="base">Copyright © 2017 Tallow Ridge Energy. All Right Reserved.</div>

</body>
</html>
```